Redesign website for small print company

Vindurgata is a small printing company in Iceland mainly servicing Students, schools, etc. We are also doing all kind of other jobs, like business cards, book printing, brochure printing etc. We are also selling books online.
Our website is: www.vindurgata.is
What we are looking for is:
- Web Design (Uncoded - PSD layout only)
- Mobile friendly design, using our current color scheme: Red, green, yellow and light gray.
- Clean simple design
- Simple, light and easy to use.
- More menu Items/drop down
Industry/Entity Type
Digital Printing
Number of Pages Required
5+ page
Requirements
Must have
- Easy navigation
- Designed for mobile
- Current color scheme (see logo)
Nice to have
- Icon based products

```html
<!DOCTYPE html>
<html lang="is">
<head>
<meta charset="utf-8">
<title>Vindurgata – Prentþjónusta</title>
<link rel="stylesheet" href="https://fonts.googleapis.com/css2?family=Open+Sans:wght@400;600;700;800&display=swap">
<style>
:root{
  --red:#ec3a33;
  --orange:#f7941d;
  --yellow:#fed603;
  --green:#0b6b33;
  --dark:#222222;
  --text:#555555;
  --muted:#888888;
  --light:#f3f3f3;
  --line:#e5e5e5;
  --white:#ffffff;
  --footer:#333333;
}
*{margin:0;padding:0;box-sizing:border-box}
html,body{width:1200px;height:3371px;overflow:hidden}
body{position:relative;background:var(--white);font-family:"Open Sans",Arial,sans-serif;color:var(--dark)}
.abs{position:absolute}

/* header */
.site-header{position:absolute;left:0;top:0;width:1200px;height:90px;z-index:5}
.brand{position:absolute;left:79px;top:26px;display:flex;align-items:center;gap:10px}
.brand-square{width:28px;height:28px;background:var(--red)}
.brand-name{font-size:24px;font-weight:700;color:var(--dark);letter-spacing:.5px}
.main-nav{position:absolute;left:546px;top:34px;display:flex;gap:36px;font-size:14px;text-transform:uppercase;color:var(--dark)}
.main-nav a{color:inherit;text-decoration:none;position:relative}
.main-nav a.active{color:var(--red)}
.main-nav a.active::after{content:"";position:absolute;left:-8px;right:-8px;top:42px;height:3px;background:var(--red)}
.header-tools{position:absolute;left:1046px;top:30px;display:flex;gap:28px;align-items:center}

/* hero */
.hero-bg{position:absolute;left:0;top:0;width:1200px;height:720px}
.hero-title{position:absolute;left:81px;top:240px;font-size:46px;line-height:58px;font-weight:700;color:var(--dark)}
.btn-primary{position:absolute;left:81px;top:382px;width:211px;height:52px;border-radius:26px;background:var(--red);color:var(--white);font-size:17px;font-weight:700;display:flex;align-items:center;justify-content:center;text-transform:uppercase}
.hero-visual{position:absolute;left:610px;top:100px;width:520px;height:470px;border-radius:40px;background:radial-gradient(circle at 50% 60%,#5fd35a 0,#e0267a 30%,#2640d6 55%,rgba(255,255,255,.85) 80%,rgba(255,255,255,0) 100%)}

/* services card */
.service-card{position:absolute;left:79px;top:611px;width:1062px;height:191px;background:var(--white);border-radius:8px;box-shadow:0 6px 24px rgba(0,0,0,.12);display:flex}
.service{flex:1;display:flex;flex-direction:column;align-items:center;justify-content:center;gap:18px;font-size:17px;color:var(--text);text-transform:uppercase}
.service+.service{border-left:1px solid var(--line)}

/* about */
.section-title{position:absolute;left:0;width:1200px;text-align:center;font-weight:700;font-size:44px}
.green{color:var(--green)}
.about-sub{position:absolute;left:0;width:1200px;top:946px;text-align:center;font-size:19px;color:var(--text)}
.about-text{position:absolute;left:262px;top:986px;width:676px;text-align:center;font-size:12.5px;line-height:22px;color:var(--muted)}
.about-text p+p{margin-top:12px}

/* products */
.products-bg{position:absolute;left:0;top:1250px;width:1200px;height:762px}
.products-title{top:1450px;color:var(--dark)}
.product{position:absolute;width:340px;text-align:center}
.product svg{display:block;margin:0 auto}
.product h3{font-size:23px;font-weight:600;margin-top:20px;color:var(--dark)}
.product p{font-size:13px;line-height:22px;color:var(--dark);margin-top:8px}

/* books */
.books-title{position:absolute;left:81px;top:2068px;font-size:44px;font-weight:700;color:var(--green)}
.slider-btn{position:absolute;top:2081px;width:62px;height:36px;border:1px solid #cccccc;border-radius:3px;display:flex;align-items:center;justify-content:center;background:var(--white)}
.book{position:absolute;top:2165px;width:300px}
.book-frame{position:absolute;left:0;top:26px;width:297px;height:274px;background:var(--red)}
.book-cover{position:absolute;left:60px;top:0;width:170px;height:270px;background:linear-gradient(90deg,#222 0 14%,#e9a91a 14% 100%);border-radius:4px}
.bag{position:absolute;left:236px;top:20px;width:74px;height:74px;border-radius:50%;background:var(--white);display:flex;align-items:center;justify-content:center}
.bag span{width:56px;height:56px;border-radius:50%;background:var(--red);display:flex;align-items:center;justify-content:center}
.book-rule{position:absolute;left:90px;top:339px;width:120px;height:3px;background:linear-gradient(90deg,var(--red),var(--orange),var(--yellow),var(--green))}
.book-price{position:absolute;left:0;width:300px;top:360px;text-align:center;font-size:27px;font-weight:600}

/* newsletter */
.news-title{top:2640px;font-size:42px;color:var(--green)}
.field{position:absolute;top:2735px;height:47px;border-radius:24px;background:var(--white);box-shadow:0 4px 16px rgba(0,0,0,.1);font-size:14px;color:var(--muted);padding-left:30px;display:flex;align-items:center}
.btn-send{position:absolute;left:858px;top:2735px;width:86px;height:47px;border-radius:24px;background:linear-gradient(90deg,var(--red),var(--orange));color:var(--white);font-weight:700;font-size:15px;display:flex;align-items:center;justify-content:center}

/* contact & map */
.map{position:absolute;left:0;top:2944px;width:1200px;height:298px;background:linear-gradient(160deg,#e8ecef 0%,#dfe6df 45%,#e9ece8 100%)}
.contact-card{position:absolute;left:79px;top:2865px;width:1062px;height:146px;background:var(--white);box-shadow:0 6px 24px rgba(0,0,0,.12);z-index:2}
.contact-item{position:absolute;top:40px;display:flex;align-items:center;gap:22px}
.contact-icon{width:62px;height:62px;border-radius:50%;border:2px solid var(--line);display:flex;align-items:center;justify-content:center}
.contact-item h4{font-size:18px;font-weight:600;color:var(--dark)}
.contact-item p{font-size:13px;line-height:20px;color:var(--text)}
.site-footer{position:absolute;left:0;top:3242px;width:1200px;height:129px;background:var(--footer);color:#dddddd;font-size:13px;display:flex;align-items:center;justify-content:center}
</style>
</head>
<body>

<svg class="hero-bg" viewBox="0 0 1200 720" aria-hidden="true">
  <defs>
    <linearGradient id="swoosh" x1="0" y1="1" x2="1" y2="0">
      <stop offset="0" stop-color="#fed603"/>
      <stop offset="0.35" stop-color="#f7941d"/>
      <stop offset="0.7" stop-color="#ec3a33"/>
      <stop offset="1" stop-color="#ec3a33"/>
    </linearGradient>
  </defs>
  <path d="M0 560 C260 430 520 360 760 250 C930 170 1070 90 1200 40 L1200 720 C1000 700 900 660 800 600 C640 520 380 520 0 675 Z" fill="url(#swoosh)"/>
  <path d="M1080 430 C1130 400 1170 380 1200 370 L1200 620 C1150 560 1110 500 1080 430 Z" fill="#0b6b33"/>
  <path d="M0 675 C380 520 640 520 800 600 L800 720 L0 720 Z" fill="#ffffff"/>
</svg>

<header class="site-header">
  <div class="brand"><span class="brand-square"></span><span class="brand-name">VINDURGATA</span></div>
  <nav class="main-nav">
    <a class="active">Home</a><a>Services</a><a>Job Submit</a><a>About us</a><a>Contact us</a>
  </nav>
  <div class="header-tools">
    <svg width="24" height="24" viewBox="0 0 24 24" fill="none" stroke="#222" stroke-width="2.4"><circle cx="10" cy="10" r="7"/><path d="M15 15l7 7"/></svg>
    <svg width="22" height="24" viewBox="0 0 22 24" fill="none" stroke="#222" stroke-width="2"><rect x="2" y="8" width="18" height="14"/><path d="M7 8V5a4 4 0 0 1 8 0v3"/></svg>
  </div>
</header>

<h1 class="hero-title">Do not worry ...<br>we'll manage Þetta</h1>
<div class="btn-primary">Know more</div>
<div class="hero-visual" role="img" aria-label="Glass jars overflowing with splashing coloured paint"></div>

<section class="service-card">
  <div class="service">
    <svg width="52" height="46" viewBox="0 0 52 46" fill="none" stroke="#f5b800" stroke-width="3"><rect x="3" y="12" width="46" height="31" rx="3"/><path d="M18 12V5h16v7M3 24h46M22 24v6h8v-6"/></svg>
    Senda verk
  </div>
  <div class="service">
    <svg width="50" height="50" viewBox="0 0 50 50" fill="none" stroke="#f5b800" stroke-width="3"><path d="M25 4a21 21 0 1 0 0 42c4 0 5-3 3-6s0-7 4-7h6c5 0 8-3 8-8C46 13 37 4 25 4z"/><circle cx="15" cy="20" r="3"/><circle cx="24" cy="13" r="3"/><circle cx="34" cy="17" r="3"/><circle cx="14" cy="31" r="3"/></svg>
    Hanna verk
  </div>
  <div class="service">
    <svg width="36" height="52" viewBox="0 0 36 52" fill="none" stroke="#f5b800" stroke-width="3.5"><path d="M5 15a13 13 0 1 1 19 11c-4 2-6 5-6 9v4"/><circle cx="18" cy="47" r="2"/></svg>
    Fa tilbod
  </div>
</section>

<h2 class="section-title green" style="top:876px">About us</h2>
<div class="about-sub">Velkomin í Vindurgata</div>
<div class="about-text">
  <p>Vindurgata er fyrirtæki staðsett á háskólasvæðinu sem hefur sérhæft sig í að þjónusta skólafólk, ásamt því að sinna öllum almennum prentun fyrir almenning.</p>
  <p>Vindurgata gefur út greinasöfn og frumsamdar kennslubækur fyrir námskeið, prentar lokaritgerðir fyrir nema, auk þess að vinna við ótalinn fjölda smærri verka fyrir nemendur, kennara og stofnanir. Má þar nefna bæklinga, skýrslur, spurningalista, nafnspjöld, bækur, OCR skönnun og fleira.</p>
  <p>Vindurgata er vottuð prentsmiðja, Laufið er opinbert umhverfismerki Norðurlandanna, sem hefur skapað sér fótfestu hér á landi og er þekkt meðal neytenda. Vindurgata er staðsett á horninu á Hrafnagötu og Norðurgötu (gengið inn Norðurgötumegin)</p>
</div>

<svg class="products-bg" viewBox="0 0 1200 762" aria-hidden="true">
  <path d="M0 30 C90 0 180 60 300 70 C420 80 460 20 600 20 C760 20 820 110 960 90 C1060 75 1130 20 1200 0 L1200 762 L0 762 Z" fill="#fed603"/>
</svg>

<h2 class="section-title products-title">Product List</h2>

<div class="product" style="left:73px;top:1530px">
  <svg width="54" height="66" viewBox="0 0 54 66" fill="none" stroke="#222" stroke-width="3"><path d="M4 3h34l12 12v48H4z"/><path d="M12 22h30M12 31h30M12 40h30M12 49h22"/></svg>
  <h3>Essays</h3>
  <p>Vindurgata prentar út og bindur inn ritgerðir.<br>Ritgerðir eru ýmist kiljuinnbundnar...</p>
</div>
<div class="product" style="left:439px;top:1530px">
  <svg width="76" height="60" viewBox="0 0 76 60" fill="none" stroke="#222" stroke-width="3"><rect x="3" y="3" width="60" height="42"/><rect x="13" y="14" width="60" height="42" fill="#fed603"/><circle cx="28" cy="32" r="6"/><path d="M20 46c2-6 14-6 16 0M44 28h20M44 36h20M44 44h14"/></svg>
  <h3>Business cards</h3>
  <p>Nafnspjöld hjá Vindurgata er hægt að prenta í<br>öllum stærðum og gerðum, en algengast...</p>
</div>
<div class="product" style="left:805px;top:1530px">
  <svg width="66" height="62" viewBox="0 0 66 62" fill="none" stroke="#222" stroke-width="3"><path d="M3 6l20-3v53L3 59zM23 3l20 6v50l-20-3zM43 9l20-6v53l-20 3z"/><path d="M9 16h8M9 26h8M29 18h8M29 28h8M49 16h8M49 26h8"/></svg>
  <h3>Leafleats</h3>
  <p>Vindurgata prentar bæklinga í öllum stærðum<br>og gerðum og á ýmsar tegundir pappírs.</p>
</div>

<div class="product" style="left:73px;top:1765px">
  <svg width="56" height="64" viewBox="0 0 56 64" fill="none" stroke="#222" stroke-width="3"><path d="M10 3h43v50H10a7 7 0 0 0 0 14h43"/><path d="M3 10v47M10 3a7 7 0 0 0-7 7"/><path d="M18 18h26"/></svg>
  <h3>Bookprinting</h3>
  <p>Vindurgata sérhæfir sig í að prenta bækur í litlu<br>upplagi, við höfum frábæran búnað til...</p>
</div>
<div class="product" style="left:439px;top:1765px">
  <svg width="54" height="66" viewBox="0 0 54 66" fill="none" stroke="#222" stroke-width="3"><path d="M8 10h38v50H8z"/><path d="M8 10a5 5 0 0 1 0-8h38a5 5 0 0 1 0 8M8 60a5 5 0 0 0 0 4h38a5 5 0 0 0 0-4"/><path d="M16 22h22M16 32h22M16 42h14"/></svg>
  <h3>Posters</h3>
  <p>Vindurgata prentar veggspjöld í öllum<br>stærðum, á pappír og striga og fleira...</p>
</div>
<div class="product" style="left:805px;top:1765px">
  <svg width="68" height="60" viewBox="0 0 68 60" fill="none" stroke="#222" stroke-width="3"><rect x="6" y="3" width="54" height="14" rx="2"/><rect x="12" y="23" width="52" height="14" rx="2"/><rect x="4" y="43" width="56" height="14" rx="2"/><path d="M14 3v14M20 23v14M12 43v14"/></svg>
  <h3>Textbooks</h3>
  <p>Vindurgata prentar út og bindur inn ritgerðir.<br>Ritgerðir eru ýmist kiljuinnbundnar...</p>
</div>

<h2 class="books-title">Online Books</h2>
<div class="slider-btn" style="left:1004px"><svg width="24" height="14" viewBox="0 0 24 14" fill="none" stroke="#333" stroke-width="2"><path d="M23 7H2M8 1L2 7l6 6"/></svg></div>
<div class="slider-btn" style="left:1079px"><svg width="24" height="14" viewBox="0 0 24 14" fill="none" stroke="#333" stroke-width="2"><path d="M1 7h21M16 1l6 6-6 6"/></svg></div>

<div class="book" style="left:94px">
  <div class="book-frame"></div>
  <div class="book-cover" role="img" aria-label="Hardcover book with a yellow cover"></div>
  <div class="bag"><span><svg width="24" height="26" viewBox="0 0 24 26" fill="none" stroke="#fff" stroke-width="2.4"><rect x="3" y="9" width="18" height="15"/><path d="M8 9V6a4 4 0 0 1 8 0v3"/></svg></span></div>
  <div class="book-rule"></div>
  <div class="book-price">$ 100</div>
</div>
<div class="book" style="left:461px">
  <div class="book-frame"></div>
  <div class="book-cover" role="img" aria-label="Hardcover book with a yellow cover"></div>
  <div class="bag"><span><svg width="24" height="26" viewBox="0 0 24 26" fill="none" stroke="#fff" stroke-width="2.4"><rect x="3" y="9" width="18" height="15"/><path d="M8 9V6a4 4 0 0 1 8 0v3"/></svg></span></div>
  <div class="book-rule"></div>
  <div class="book-price">$ 100</div>
</div>
<div class="book" style="left:828px">
  <div class="book-frame"></div>
  <div class="book-cover" role="img" aria-label="Hardcover book with a yellow cover"></div>
  <div class="bag"><span><svg width="24" height="26" viewBox="0 0 24 26" fill="none" stroke="#fff" stroke-width="2.4"><rect x="3" y="9" width="18" height="15"/><path d="M8 9V6a4 4 0 0 1 8 0v3"/></svg></span></div>
  <div class="book-rule"></div>
  <div class="book-price">$ 100</div>
</div>

<h2 class="section-title news-title">Subcribe to our Newsletter</h2>
<div class="field" style="left:272px;width:326px">Name</div>
<div class="field" style="left:620px;width:324px">Email</div>
<div class="btn-send">SEND</div>

<div class="map" role="img" aria-label="Map showing the shop location"></div>
<section class="contact-card">
  <div class="contact-item" style="left:54px">
    <div class="contact-icon"><svg width="20" height="26" viewBox="0 0 20 26"><path d="M10 1a9 9 0 0 0-9 9c0 7 9 15 9 15s9-8 9-15a9 9 0 0 0-9-9z" fill="#ec3a33"/><circle cx="10" cy="10" r="3.2" fill="#fff"/></svg></div>
    <p>Lorem Ipsum is simply dummy<br>text of the printing.</p>
  </div>
  <div class="contact-item" style="left:390px">
    <div class="contact-icon"><svg width="22" height="22" viewBox="0 0 24 24"><path d="M6 2l4 5-2 3c1 3 3 5 6 6l3-2 5 4-2 4C11 22 2 13 2 4z" fill="#ec3a33"/></svg></div>
    <div><h4>Phone</h4><p>555 0142</p></div>
  </div>
  <div class="contact-item" style="left:710px">
    <div class="contact-icon"><svg width="22" height="16" viewBox="0 0 22 16" fill="none" stroke="#ec3a33" stroke-width="2"><rect x="1" y="1" width="20" height="14"/><path d="M1 1l10 8 10-8"/></svg></div>
    <div><h4>Email</h4><p>verk@vindurgata.is</p></div>
  </div>
</section>

<footer class="site-footer">©VINDURGATA- 2018. All Rights Reserved.</footer>

</body>
</html>
```